Business Card - high end, modern health care

Hey designers!

We need a double sided business card for the boutique, cutting edge physical therapy rehabilitation centre in Sydney's Northern Beaches.

With the most qualified physios in the area The Harbourview Motion Clinic does what other physiotherapy practices do not, we take our time with our patients giving them longer appointments, better physios and therefor faster results!

We guarantee that the service people receive at THMC will be unparalleled.

Hence we need a business card to reflect our modern, boutique, high end service. The final design needs to reflect that we are in a class of our own yet with the feel of beachside retreat.

Below I have attached our logo in both blue on white and white on blue. The exact colour is;
and the font that we have used in our logo is Tex Gyre Aventador.

I like the idea of the blue as the main colour as it is more eye catching and our signage onto the main road will be in this blue and in the interest of consistency across marketing the blue needs to be a part of the design. However I would appreciate a few designs onto a wooden background as this is a visual theme within the fitout of the practice.

The design needs to be of standard size (91x55mm).

Target Market(s)

We target people who have an end outcome in mind and those who have had poor experiences with other providers and ensure that everyone gets the care that they deserve with a premium service that is tailored to the individuals circumstances. As a premium service, the target market is highly educated, business and tech savvy with the additional target market of elderly people who have self funded their retirement and see value in paying for the best ongoing rehabilitation to maintain independence.

Industry/Entity Type

Physical Therapy

Contact Information for Business Card

Name, designation( Titled Musculoskeletal Physiotherapist... there will also be those in the company that have multiple designations ie 5 or 6 words long), phone number, email, facebook, instagram, address

Font styles to use
Sans Serif

Colors

Designer to choose colors to be used in the design.

Requirements
Must have
• Front - The logo as large as possible, blue or wooden theme, and all of the important details.
• Back - A blank space/lines on which to write appointment times (no "Appointment, date, time" etc.)
Nice to have
• facebook url
• logos for facebook and instagram
• Mini logos for the phone and email?

```html
<!DOCTYPE html>
<html lang="en">
<head>
<meta charset="utf-8">
<title>The Harbourview Motion Clinic – Business Card</title>
<link rel="stylesheet" href="https://fonts.googleapis.com/css2?family=Raleway:wght@400;500;700&display=swap">
<style>
  :root {
    --backdrop: #4b4a72;
    --brand-blue: #0c56a6;
    --paper: #ffffff;
    --faint-blue: #e3e7f3;
    --rule: #aab5d6;
  }
  * { box-sizing: border-box; margin: 0; padding: 0; }
  html, body { width: 1200px; height: 1000px; overflow: hidden; }
  body {
    position: relative;
    background: var(--backdrop);
    font-family: "Raleway", sans-serif;
  }
  .card {
    position: absolute;
    overflow: hidden;
    background: var(--paper);
    box-shadow: 0 8px 18px rgba(0, 0, 0, 0.35);
  }

  /* Back of card */
  .card-back { left: 136px; top: 78px; width: 660px; height: 377px; }
  .card-back .wordmark {
    position: absolute; left: 42px; top: 42px;
    display: flex; align-items: center; gap: 10px;
    color: var(--brand-blue);
  }
  .wordmark-dot {
    width: 54px; height: 54px; border-radius: 50%;
    background: var(--brand-blue); flex: none;
  }
  .wordmark-name {
    font-weight: 700; line-height: 1.05; letter-spacing: 0.04em;
    text-transform: uppercase;
  }
  .card-back .wordmark-name { font-size: 25px; }
  .decor-circle {
    position: absolute; left: 332px; top: 42px;
    width: 298px; height: 298px; border-radius: 50%;
    background: var(--faint-blue);
  }

  /* Front of card */
  .card-front { left: 400px; top: 535px; width: 657px; height: 375px; }
  .front-band {
    position: absolute; inset: 0 0 72px 0;
    background: var(--brand-blue); color: var(--paper);
  }
  .contact { position: absolute; left: 49px; top: 68px; }
  .person-name { font-size: 25px; font-weight: 400; }
  .designation { font-size: 15px; margin-top: 8px; }
  .contact-list { list-style: none; margin-top: 22px; }
  .contact-item {
    display: flex; align-items: center; gap: 16px;
    font-size: 17px; height: 31px;
  }
  .contact-item.social { font-size: 15px; height: 34px; }
  .contact-item.social.first { margin-top: 9px; }
  .contact-item svg { width: 22px; height: 22px; flex: none; }
  .social-dot {
    width: 24px; height: 24px; border-radius: 50%;
    background: var(--paper); flex: none;
  }
  .divider {
    position: absolute; left: 344px; top: 70px;
    width: 2px; height: 214px; background: var(--paper); opacity: 0.85;
  }
  .front-mark {
    position: absolute; left: 410px; top: 72px; width: 200px;
    display: flex; flex-direction: column; align-items: center;
  }
  .front-mark .mark-circle {
    width: 150px; height: 150px; border-radius: 50%; background: var(--paper);
  }
  .front-mark .wordmark-name {
    margin-top: 18px; font-size: 17px; text-align: center;
  }
  .write-line {
    position: absolute; left: 50px; right: 38px; bottom: 26px;
    border-top: 2px dashed var(--rule);
  }
</style>
</head>
<body>

<section class="card card-back">
  <div class="wordmark">
    <span class="wordmark-dot"></span>
    <span class="wordmark-name">The Harbourview<br>Motion Clinic</span>
  </div>
  <div class="decor-circle"></div>
</section>

<section class="card card-front">
  <div class="front-band">
    <div class="contact">
      <p class="person-name">Name of Person</p>
      <p class="designation">Designation</p>
      <ul class="contact-list">
        <li class="contact-item">
          <svg viewBox="0 0 24 24" fill="none" stroke="#fff" stroke-width="1.6">
            <circle cx="12" cy="12" r="10.5"/>
            <path d="M8.5 7.5c.6-.6 1.3-.6 1.8 0l1 1.4c.4.5.3 1.1-.2 1.5l-.6.5c.5 1.2 1.4 2.1 2.6 2.6l.5-.6c.4-.5 1-.6 1.5-.2l1.4 1c.6.5.6 1.2 0 1.8-.9.9-2.2 1.1-3.4.5-2.4-1.1-4.2-2.9-5.3-5.3-.6-1.2-.4-2.5.7-3.2z" fill="#fff" stroke="none"/>
          </svg>
          <span>555.014.2870</span>
        </li>
        <li class="contact-item">
          <svg viewBox="0 0 24 24" fill="none" stroke="#fff" stroke-width="1.6">
            <rect x="2" y="5" width="20" height="14"/>
            <path d="M2 5l10 8 10-8M2 19l7-7M22 19l-7-7"/>
          </svg>
          <span>hello@harbourviewmotion.com</span>
        </li>
        <li class="contact-item social first">
          <span class="social-dot"></span>
          <span>/harbourviewmotion</span>
        </li>
        <li class="contact-item social">
          <span class="social-dot"></span>
          <span>@harbourview_motion</span>
        </li>
      </ul>
    </div>
    <div class="divider"></div>
    <div class="front-mark">
      <span class="mark-circle"></span>
      <span class="wordmark-name">The Harbourview<br>Motion Clinic</span>
    </div>
  </div>
  <div class="write-line"></div>
</section>

</body>
</html>
```